Business Card for beauty technology startup

Design Glimora Business Card for a Beauty, based on the website identity and colors (https://www.glimora-example.com).
Glimora is a beauty tech startup that gathers helpful product info for beauty lovers and consumers (such as availability on stores, price range and product reviews) for makeup products. The card design must be young, colorful but clean, and very modern.

Target Market(s)

woman, 15-35

Industry/Entity Type

Cosmetics

Contact Information for Business Card

Full Name, address, phone

Font styles to use
Other font styles liked:
• Advent Pro

Colors
e34297
86cfc6
ffffff
5c5c5c
e8e8e8
e667a6
b2b2b2

Requirements
Must have
• One full colored side with a creative design and another with card info
• Use Color palette: #95C5C5 and/or #D38AA5
• Use fonts: Advent Pro
• Use website identity: https://www.glimora-example.com
Nice to have
• If needed extra font: Roboto

```html
<!DOCTYPE html>
<html lang="en">
<head>
<meta charset="utf-8">
<title>Glimora Business Card</title>
<link rel="stylesheet" href="https://fonts.googleapis.com/css2?family=Open+Sans:wght@300;400;600&display=swap">
<style>
  :root {
    --page-bg: #2a2624;
    --card-black: #0e0d0e;
    --card-edge: #1a1819;
    --rose: #d38aa5;
    --rose-deep: #e34297;
    --teal: #95c5c5;
    --teal-bright: #86cfc6;
    --ink-white: #f2f2f2;
    --divider: #6a4a58;
  }
  * { margin: 0; padding: 0; box-sizing: border-box; }
  html, body {
    width: 1200px;
    height: 900px;
    overflow: hidden;
    background: var(--page-bg);
    font-family: "Open Sans", Arial, sans-serif;
  }
  .stage {
    width: 1200px;
    height: 900px;
    display: flex;
    align-items: center;
    justify-content: center;
    gap: 40px;
  }
  .card {
    width: 520px;
    height: 300px;
    border: 1px solid var(--card-edge);
    position: relative;
    overflow: hidden;
    box-shadow: 0 10px 24px rgba(0, 0, 0, 0.45);
  }

  /* Info side */
  .card-info { background: var(--card-black); }
  .card-info .brand-block {
    position: absolute;
    left: 0;
    top: 0;
    width: 228px;
    height: 300px;
    display: flex;
    flex-direction: column;
    align-items: center;
    justify-content: center;
    gap: 14px;
  }
  .brand-dot {
    width: 92px;
    height: 92px;
    border: 3px solid var(--rose);
    border-radius: 50%;
  }
  .brand-name-rose {
    font-weight: 400;
    font-size: 26px;
    color: var(--rose);
    letter-spacing: 1px;
  }
  .card-info .divider {
    position: absolute;
    left: 228px;
    top: 66px;
    width: 1px;
    height: 168px;
    background: var(--divider);
  }
  .contact {
    position: absolute;
    left: 256px;
    top: 72px;
    color: var(--ink-white);
    font-size: 14px;
    line-height: 1.35;
  }
  .person-name {
    color: var(--rose);
    font-weight: 600;
    font-size: 16px;
    text-transform: uppercase;
    letter-spacing: 0.3px;
  }
  .person-role { margin-bottom: 8px; color: var(--teal-bright); }
  .contact-list { list-style: none; }
  .contact-list li {
    display: flex;
    align-items: center;
    gap: 8px;
    margin-bottom: 2px;
  }
  .contact-list svg { width: 12px; height: 12px; flex: none; }
  .icon-fill { fill: var(--rose); }
  .icon-line { fill: none; stroke: var(--rose); stroke-width: 2.4; stroke-linejoin: round; }
  .address { margin-top: 10px; }
  .accent-band {
    position: absolute;
    left: 0;
    bottom: 0;
    width: 100%;
    height: 6px;
    background: linear-gradient(90deg, var(--rose), var(--teal));
  }

  /* Brand side, full colour */
  .card-brand {
    background: linear-gradient(135deg, var(--rose) 0%, #c9a3b8 45%, var(--teal) 100%);
    display: flex;
    align-items: center;
    justify-content: center;
    gap: 22px;
  }
  .brand-dot-white {
    width: 70px;
    height: 70px;
    border: 2px solid #ffffff;
    border-radius: 50%;
  }
  .brand-name-white {
    font-weight: 300;
    font-size: 40px;
    color: #ffffff;
    letter-spacing: 8px;
    text-transform: uppercase;
  }
</style>
</head>
<body>
<main class="stage">
  <section class="card card-info">
    <div class="brand-block">
      <div class="brand-dot"></div>
      <div class="brand-name-rose">Glimora</div>
    </div>
    <div class="divider"></div>
    <div class="contact">
      <div class="person-name">Daniel Hartley</div>
      <div class="person-role">Managing Director</div>
      <ul class="contact-list">
        <li>
          <svg viewBox="0 0 24 24" aria-hidden="true"><path class="icon-fill" d="M6.6 10.8a15.1 15.1 0 0 0 6.6 6.6l2.2-2.2a1 1 0 0 1 1-.25 11.4 11.4 0 0 0 3.6.57 1 1 0 0 1 1 1V20a1 1 0 0 1-1 1A17 17 0 0 1 3 4a1 1 0 0 1 1-1h3.5a1 1 0 0 1 1 1c0 1.25.2 2.45.57 3.6a1 1 0 0 1-.25 1z"/></svg>
          (044)987650321
        </li>
        <li>
          <svg viewBox="0 0 24 24" aria-hidden="true"><rect class="icon-line" x="2.5" y="5" width="19" height="14"/><path class="icon-line" d="M2.5 5l9.5 8 9.5-8"/></svg>
          hello@glimora-mail.com
        </li>
        <li>
          <svg viewBox="0 0 24 24" aria-hidden="true"><circle class="icon-fill" cx="12" cy="12" r="9"/></svg>
          www.glimora-example.com
        </li>
      </ul>
      <div class="address">4821, Rosewood Lane,<br>Northvale, 54320</div>
    </div>
    <div class="accent-band"></div>
  </section>

  <section class="card card-brand">
    <div class="brand-dot-white"></div>
    <div class="brand-name-white">Glimora</div>
  </section>
</main>
</body>
</html>
```